Fitness Equipment Repair Business Needs a Catchy New Business Card

We have an existing business card, however, it is quite plain and boring. We are expanding primarily in the commercial area (gyms, studios, apartment complexes etc). The business card will serve as eye candy to those managers/owners that can't be met for a face to face.
Originally I was planning for a brochure as well, but all of our information is better summarized on our website. (brightloopservice.ca).
I would like the card to match the colour scheme of the website and utilize the logo. It should have a professional clean feel to it, however, a little colouring outside the lines wouldn't hurt.
The example card is for my service technician (Colin Marsh). If possible I would like to be able to edit the text to use for more than one person.

Industry/Entity Type

Appliance Repair

Contact Information for Business Card

Clean, crisp and professional but needs to be eye catching. Preferably using the black, white and red colour scheme matching the website. Double sided would be nice, but is not necessary.

Colors
ec1f27
ffffff
000000

Requirements
Must have
• Must be able to edit name, phone number and title to use for multiple people. Must show the company website (brightloopservice.ca).

```html
<!DOCTYPE html>
<html lang="en">
<head>
<meta charset="utf-8">
<title>Bright Loop Service – Business Card</title>
<link href="https://fonts.googleapis.com/css2?family=Cinzel:wght@500&family=Source+Sans+3:wght@400;600&family=Tinos:wght@700&display=swap" rel="stylesheet">
<style>
  :root {
    --brand-red: #ec1f27;
    --brand-black: #000000;
    --brand-white: #ffffff;
    --ink: #111111;
    --card-top: #f6f6f6;
    --card-bottom: #ffffff;
    --page-bg: #e4e4e4;
  }
  * { margin: 0; padding: 0; box-sizing: border-box; }
  html, body {
    width: 1200px; height: 900px; overflow: hidden;
    background: var(--page-bg);
  }
  .card {
    position: absolute; left: 160px; top: 180px;
    width: 880px; height: 540px;
    border-radius: 24px; overflow: hidden;
    background: linear-gradient(180deg, var(--card-top), var(--card-bottom));
    box-shadow: 0 10px 30px rgba(0,0,0,0.15);
    font-family: "Source Sans 3", "Myriad Pro", sans-serif;
    color: var(--ink);
  }
  .brand-mark {
    position: absolute; left: 74px; top: 60px;
    width: 130px; display: flex; flex-direction: column; align-items: center; gap: 12px;
  }
  .brand-mark__dot {
    width: 110px; height: 110px; border-radius: 50%;
    background: var(--brand-black);
  }
  .brand-mark__name {
    font-size: 20px; font-weight: 600; color: var(--brand-black); white-space: nowrap;
  }
  .company-name {
    position: absolute; left: 228px; top: 100px; width: 580px;
    text-align: center;
    font-family: "Cinzel", serif; font-weight: 500;
    font-size: 46px; letter-spacing: 1px; color: var(--ink);
  }
  .contact {
    position: absolute; left: 160px; top: 196px; width: 560px;
    text-align: center;
  }
  .contact__name { font-size: 31px; font-weight: 600; line-height: 38px; }
  .contact__title { font-size: 23px; line-height: 30px; }
  .contact__address { font-size: 23px; margin-top: 14px; line-height: 30px; }
  .contact__lines { font-size: 23px; margin-top: 16px; line-height: 32px; white-space: nowrap; }
  .contact__lines b { font-weight: 600; }
  .contact__lines .gap { display: inline-block; width: 22px; }
  .contact__web { font-weight: 600; }
  .rule-red {
    position: absolute; left: 0; top: 424px; width: 100%; height: 11px;
    background: var(--brand-red);
  }
  .tagline-band {
    position: absolute; left: 0; top: 437px; width: 100%; height: 103px;
    background: var(--brand-black);
    display: flex; align-items: center; justify-content: center;
  }
  .tagline {
    font-family: "Tinos", "Times New Roman", serif; font-weight: 700;
    font-size: 29px; color: var(--brand-white);
  }
</style>
</head>
<body>
  <div class="card">
    <div class="brand-mark">
      <span class="brand-mark__dot"></span>
      <span class="brand-mark__name">Bright Loop</span>
    </div>

    <h1 class="company-name">Bright Loop Service</h1>

    <div class="contact">
      <p class="contact__name">Colin Marsh</p>
      <p class="contact__title">Managing Director</p>
      <p class="contact__address">1234, Address GoesHere, Country, 12345</p>
      <p class="contact__lines"><b>P:</b> (044) 555014720<span class="gap"></span><b>M:</b> (044)555019384</p>
      <p class="contact__lines" style="margin-top:0"><b>E:</b> info@brightloop.ca<span class="gap"></span><span class="contact__web">www.brightloopservice.ca</span></p>
    </div>

    <div class="rule-red"></div>
    <div class="tagline-band">
      <p class="tagline">When your equipment can't finish their workout, give us a call!</p>
    </div>
  </div>
</body>
</html>
```